A weight loss and fitness website design

I am into different types of modern weight loss techniques for people who are a little fatty and wish to be physically and mentally fit. Basically, the website is to teach people how to reduce weight using different methods such as diet, exercises, yoga and other forms. I would need an eye catching website which would make visitors want to come back. The will be also be different forms of exercises for a health and fit life. This said, my website is to have two categories of
1) weight loss techniques
2) exercise of fit and healthy living.
I prefer bright colors such as green, blue, yellow, and orange. Imagery should include before and after pictures of people suffering from obesity, people under going exercises.
Designers can get ideas and inspiration from the website fitlumen.com which i was previously part of the team.
Target Market(s)
My target audience are people suffering from obesity, malnutrition and physical deficiency.
Industry/Entity Type
Fitness
Coding
Coded - Design and coding required
Number of Pages Required
1 page
Look and feel

```html
<!DOCTYPE html>
<html lang="en">
<head>
<meta charset="utf-8">
<title>Vireo Fitness</title>
<link rel="stylesheet" href="https://fonts.googleapis.com/css2?family=Open+Sans:wght@300;400;600;700&display=swap">
<style>
:root{
  --brand-blue:#1a5cc0;
  --section-blue:#0b46a4;
  --section-green:#0aa548;
  --title-green:#109a45;
  --accent-yellow:#f3dc3a;
  --accent-orange:#f39a12;
  --ink:#333;
  --muted:#8a8a8a;
  --light-band:#efefef;
  --footer:#1e1e22;
  --white:#fff;
}
*{box-sizing:border-box;margin:0;padding:0}
html,body{width:1200px;height:3896px;overflow:hidden}
body{font-family:"Open Sans",Arial,sans-serif;color:var(--ink);background:var(--white)}
.container{width:930px;margin:0 auto;position:relative}

/* header */
.site-header{height:78px;background:var(--white)}
.site-header .container{display:flex;align-items:center;height:78px;justify-content:space-between}
.logo{font-size:32px;font-weight:400;color:var(--brand-blue);letter-spacing:.2px}
.main-nav{display:flex;align-items:center;gap:26px;font-size:12px;color:#444}
.main-nav .nav-button{background:var(--accent-orange);color:var(--white);padding:7px 13px;font-size:12px}

/* hero */
.hero{height:436px;position:relative;background:linear-gradient(100deg,#8a8f96 0%,#c9c4bd 35%,#e4e6e9 62%,#9da3aa 82%,#55595e 100%)}
.hero-caption{position:absolute;left:792px;top:228px;width:278px;height:130px;background:rgba(255,255,255,.88);padding:14px 20px;text-align:right}
.hero-caption h2{font-size:25px;font-weight:300;line-height:31px;color:#333}
.hero-caption p{font-size:10px;color:#777;margin-top:6px;line-height:14px}
.slider-dots{position:absolute;left:0;right:0;top:478px;display:flex;justify-content:center;gap:10px}
.slider-dots span{width:9px;height:9px;border-radius:50%;background:rgba(255,255,255,.6)}
.slider-dots span.active{background:var(--white)}
.slider-dots{top:478px;position:absolute}

/* welcome */
.welcome{height:200px;text-align:center;padding-top:40px}
.welcome h1{font-size:33px;font-weight:600;color:var(--title-green)}
.welcome p{font-size:11px;line-height:18px;color:var(--muted);margin-top:12px}

/* category sections */
.category{color:var(--white);padding-top:50px}
.category.blue{background:var(--section-blue);height:932px}
.category.green{background:var(--section-green);height:935px}
.intro-row{display:flex;justify-content:space-between;height:160px;margin-bottom:50px}
.intro-row .intro-text{width:600px;padding-top:0}
.intro-row h2{font-size:31px;font-weight:400;color:var(--accent-yellow);margin-bottom:14px}
.intro-row p,.feature-text p{font-size:12.5px;line-height:21px}
.intro-photo{width:302px;height:143px;border:3px solid #e6e6e6}
.feature-row{display:flex;align-items:center;height:172px;margin-bottom:48px;gap:26px}
.feature-row.reverse{flex-direction:row-reverse}
.feature-photo{width:172px;height:172px;border-radius:50%;border:5px solid var(--white);flex:none}
.feature-text{flex:1}
.feature-text h3{font-size:30px;font-weight:300;margin-bottom:10px}

/* promo bands */
.promo{height:320px;position:relative;background:var(--light-band)}
.promo h2{font-size:31px;font-weight:300;line-height:39px;color:#333}
.promo p{font-size:12px;line-height:19px;color:#777;margin-top:12px}
.promo-one .promo-text{position:absolute;left:135px;top:84px;width:420px}
.promo-one .promo-photo{position:absolute;left:690px;top:0;width:400px;height:320px;background:radial-gradient(ellipse at 50% 55%,#b88e6c 0%,#9a6f4f 35%,rgba(239,239,239,0) 68%)}
.promo-two{height:325px;background:linear-gradient(90deg,#e9e4de 0%,#f4f1ee 40%,#f6f6f6 100%)}
.promo-two .promo-photo{position:absolute;left:90px;top:0;width:440px;height:325px;background:radial-gradient(ellipse at 45% 50%,#e8c9a8 0%,#d9b793 30%,#a9b8c7 55%,rgba(246,246,246,0) 75%)}
.promo-two .promo-text{position:absolute;left:670px;top:92px;width:420px}

/* testimonials */
.testimonials{height:358px;background:#f3f3f3;padding-top:36px}
.testimonials h2{text-align:center;font-size:28px;font-weight:600;color:#333}
.testimonial-list{display:flex;justify-content:space-between;margin-top:28px}
.testimonial{width:300px}
.testimonial-card{position:relative;background:var(--white);height:148px;padding:18px 22px}
.testimonial-card::after{content:"";position:absolute;right:0;bottom:-18px;border-top:18px solid var(--white);border-left:24px solid transparent}
.quote-mark{display:block;width:26px;height:20px;margin-bottom:8px}
.testimonial-card p{font-size:10.5px;line-height:16px;color:#888}
.testimonial-author{text-align:right;margin-top:26px;padding-right:4px}
.testimonial-author strong{display:block;font-size:13px;font-weight:400;color:var(--title-green)}
.testimonial-author span{font-size:10px;color:#888}
.testimonial-dots{display:flex;justify-content:center;gap:12px;margin-top:20px}
.testimonial-dots span{width:8px;height:8px;border-radius:50%;background:#c9c9c9}
.testimonial-dots span.active{background:#555}

/* call to action */
.cta{height:182px;text-align:center;padding-top:52px}
.cta h2{font-size:32px;font-weight:400;color:var(--brand-blue)}
.cta .button{display:inline-block;margin-top:12px;background:var(--section-blue);color:var(--white);font-size:11px;padding:8px 16px}

/* footer */
.site-footer{height:130px;background:var(--footer);text-align:center;padding-top:22px;color:#aaa}
.social{display:flex;justify-content:center;gap:20px}
.social span{width:14px;height:14px;border-radius:50%;background:#9a9a9a}
.footer-nav{font-size:11px;margin-top:16px;color:#bbb}
.footer-nav span{margin:0 10px}
.copyright{font-size:10px;margin-top:10px;color:#777}
</style>
</head>
<body>

<header class="site-header">
  <div class="container">
    <div class="logo">Vireo Fitness</div>
    <nav class="main-nav">
      <span>Home</span><span>About us</span><span>Trainings</span><span>Classes</span><span>Testimonials</span><span>Contact us</span>
      <span class="nav-button">Join</span>
    </nav>
  </div>
</header>

<section class="hero" role="img" aria-label="Trainer helping a man lift a dumbbell in a gym">
  <div class="hero-caption">
    <h2>Donec gravida scelerisque pretium</h2>
    <p>Phasellus non neque at risus auctor laoreet a ut velit. Sed odio nisl, ultricies eget congue.</p>
  </div>
  <div class="slider-dots"><span></span><span class="active"></span><span></span><span></span></div>
</section>

<section class="welcome">
  <div class="container">
    <h1>Welcome to Vireo Fitness</h1>
    <p>Donec id ex consequat, viverra augue id, ultricies mi. Nunc volutpat condimentum velit, vitae consectetur ante suscipit ac. Nullam eget ornare ex, quis ullamcorper purus. Sed eget libero purus. Vivamus non ornare tortor. Donec vitae gravida ligula, ac vestibulum leo. Etiam non lacus id elit tincidunt hendrerit. Quisque iaculis blandit viverra. Nulla facilisi. Nam nisl elit, dictum non nisl vel, pulvinar sodales nisl. Maecenas quis maximus turpis. Duis tempor, lectus id mattis vehicula.</p>
  </div>
</section>

<section class="category blue">
  <div class="container">
    <div class="intro-row">
      <div class="intro-text">
        <h2>Weight Loss Techniques</h2>
        <p>Donec id ex consequat, viverra augue id, ultricies mi. Nunc volutpat condimentum velit, vitae consectetur ante suscipit ac. Nullam eget ornare ex, quis ullamcorper purus. Sed eget libero purus. Vivamus non ornare tortor. Donec vitae gravida ligula, ac vestibulum leo. Etiam non lacus id elit tincidunt hendrerit. Quisque iaculis blandit viverra. Nulla facilisi. Nam nisl elit, dictum non nisl vel, pulvinar sodales nisl. Maecenas quis maximus turpis. Duis tempor, lectus id mattis vehicula. Suspendisse tempus efficitur auctor.</p>
      </div>
      <div class="intro-photo" role="img" aria-label="Before and after photos of a man's torso" style="background:linear-gradient(90deg,#b08466 0%,#c99c7c 30%,#9f7257 50%,#c0906f 75%,#a87a5d 100%)"></div>
    </div>
    <div class="feature-row">
      <div class="feature-photo" role="img" aria-label="Measuring tape around a slim waist" style="background:radial-gradient(circle,#d9b090 0%,#c99474 50%,#8a8f8c 100%)"></div>
      <div class="feature-text">
        <h3>Faster Results</h3>
        <p>Phasellus non neque at risus auctor laoreet a ut velit. Sed odio nisl, ultricies eget congue in, varius id sem. Phasellus at orci a mauris gravida bibendum. Integer quis lacus eu enim ornare condimentum. Integer varius, ex a ullamcorper ullamcorper, metus ante facilisis enim, at tempus justo nisi sed diam. Sed tempor tincidunt luctus. Cras vel elit at lorem consequat pulvinar eget quis purus. Nulla pharetra ullamcorper dictum. Fusce efficitur urna at mi interdum, eget hendrerit purus eleifend. Suspendisse pulvinar accumsan mi eget ornare. Donec pulvinar elit sit amet tempor luctus.</p>
      </div>
    </div>
    <div class="feature-row reverse">
      <div class="feature-photo" role="img" aria-label="Fruit slices and a notebook with a workout plan" style="background:radial-gradient(circle,#f3c46a 0%,#e8a24a 45%,#cfd4d6 100%)"></div>
      <div class="feature-text">
        <h3>Workout Schedules</h3>
        <p>Phasellus non neque at risus auctor laoreet a ut velit. Sed odio nisl, ultricies eget congue in, varius id sem. Phasellus at orci a mauris gravida bibendum. Integer quis lacus eu enim ornare condimentum. Integer varius, ex a ullamcorper ullamcorper, metus ante facilisis enim, at tempus justo nisi sed diam. Sed tempor tincidunt luctus. Cras vel elit at lorem consequat pulvinar eget quis purus. Nulla pharetra ullamcorper dictum. Fusce efficitur urna at mi interdum, eget hendrerit purus eleifend. Suspendisse pulvinar accumsan mi eget ornare. Donec pulvinar elit sit amet tempor luctus.</p>
      </div>
    </div>
    <div class="feature-row">
      <div class="feature-photo" role="img" aria-label="Woman jogging along a green park path" style="background:radial-gradient(circle,#b9d98a 0%,#7fb552 50%,#4d8a3a 100%)"></div>
      <div class="feature-text">
        <h3>Diet Plans</h3>
        <p>Phasellus non neque at risus auctor laoreet a ut velit. Sed odio nisl, ultricies eget congue in, varius id sem. Phasellus at orci a mauris gravida bibendum. Integer quis lacus eu enim ornare condimentum. Integer varius, ex a ullamcorper ullamcorper, metus ante facilisis enim, at tempus justo nisi sed diam. Sed tempor tincidunt luctus. Cras vel elit at lorem consequat pulvinar eget quis purus. Nulla pharetra ullamcorper dictum. Fusce efficitur urna at mi interdum, eget hendrerit purus eleifend. Suspendisse pulvinar accumsan mi eget ornare. Donec pulvinar elit sit amet tempor luctus.</p>
      </div>
    </div>
  </div>
</section>

<section class="promo promo-one">
  <div class="promo-text">
    <h2>Proin ac eros quis sem bibendum</h2>
    <p>Fusce efficitur urna at mi interdum, eget hendrerit purus eleifend. Suspendisse pulvinar accumsan mi eget ornare. Donec pulvinar elit sit amet tempor luctus.</p>
  </div>
  <div class="promo-photo" role="img" aria-label="Muscular man lifting a dumbbell"></div>
</section>

<section class="category green">
  <div class="container">
    <div class="intro-row">
      <div class="intro-text">
        <h2>Exercise of Fit and Healthy Living</h2>
        <p>Donec id ex consequat, viverra augue id, ultricies mi. Nunc volutpat condimentum velit, vitae consectetur ante suscipit ac. Nullam eget ornare ex, quis ullamcorper purus. Sed eget libero purus. Vivamus non ornare tortor. Donec vitae gravida ligula, ac vestibulum leo. Etiam non lacus id elit tincidunt hendrerit. Quisque iaculis blandit viverra. Nulla facilisi. Nam nisl elit, dictum non nisl vel, pulvinar sodales nisl. Maecenas quis maximus turpis. Duis tempor, lectus id mattis vehicula. Suspendisse tempus efficitur auctor.</p>
      </div>
      <div class="intro-photo" role="img" aria-label="Athlete training with weights in a gym" style="background:linear-gradient(90deg,#e8e8e8 0%,#9a9a9a 35%,#4a3a30 55%,#8d8d8d 75%,#d8d8d8 100%)"></div>
    </div>
    <div class="feature-row">
      <div class="feature-photo" role="img" aria-label="Man working out with weights" style="background:radial-gradient(circle,#7a4d35 0%,#4a2d20 50%,#1f1a18 100%)"></div>
      <div class="feature-text">
        <h3>Workout with weights</h3>
        <p>Phasellus non neque at risus auctor laoreet a ut velit. Sed odio nisl, ultricies eget congue in, varius id sem. Phasellus at orci a mauris gravida bibendum. Integer quis lacus eu enim ornare condimentum. Integer varius, ex a ullamcorper ullamcorper, metus ante facilisis enim, at tempus justo nisi sed diam. Sed tempor tincidunt luctus. Cras vel elit at lorem consequat pulvinar eget quis purus. Nulla pharetra ullamcorper dictum. Fusce efficitur urna at mi interdum, eget hendrerit purus eleifend. Suspendisse pulvinar accumsan mi eget ornare. Donec pulvinar elit sit amet tempor luctus.</p>
      </div>
    </div>
    <div class="feature-row reverse">
      <div class="feature-photo" role="img" aria-label="Person meditating in a yoga pose by the sea" style="background:radial-gradient(circle,#f3efe6 0%,#d8e2e6 55%,#a9bfc9 100%)"></div>
      <div class="feature-text">
        <h3>Yoga for mind</h3>
        <p>Phasellus non neque at risus auctor laoreet a ut velit. Sed odio nisl, ultricies eget congue in, varius id sem. Phasellus at orci a mauris gravida bibendum. Integer quis lacus eu enim ornare condimentum. Integer varius, ex a ullamcorper ullamcorper, metus ante facilisis enim, at tempus justo nisi sed diam. Sed tempor tincidunt luctus. Cras vel elit at lorem consequat pulvinar eget quis purus. Nulla pharetra ullamcorper dictum. Fusce efficitur urna at mi interdum, eget hendrerit purus eleifend. Suspendisse pulvinar accumsan mi eget ornare. Donec pulvinar elit sit amet tempor luctus.</p>
      </div>
    </div>
    <div class="feature-row">
      <div class="feature-photo" role="img" aria-label="Woman sitting with small dumbbells" style="background:radial-gradient(circle,#f2c9c9 0%,#e79aa8 40%,#f6f6f6 100%)"></div>
      <div class="feature-text">
        <h3>Calories counter</h3>
        <p>Phasellus non neque at risus auctor laoreet a ut velit. Sed odio nisl, ultricies eget congue in, varius id sem. Phasellus at orci a mauris gravida bibendum. Integer quis lacus eu enim ornare condimentum. Integer varius, ex a ullamcorper ullamcorper, metus ante facilisis enim, at tempus justo nisi sed diam. Sed tempor tincidunt luctus. Cras vel elit at lorem consequat pulvinar eget quis purus. Nulla pharetra ullamcorper dictum. Fusce efficitur urna at mi interdum, eget hendrerit purus eleifend. Suspendisse pulvinar accumsan mi eget ornare. Donec pulvinar elit sit amet tempor luctus.</p>
      </div>
    </div>
  </div>
</section>

<section class="promo promo-two">
  <div class="promo-photo" role="img" aria-label="Slim woman holding out oversized jeans after weight loss"></div>
  <div class="promo-text">
    <h2>Proin ac eros quis sem bibendum</h2>
    <p>Fusce efficitur urna at mi interdum, eget hendrerit purus eleifend. Suspendisse pulvinar accumsan mi eget ornare. Donec pulvinar elit sit amet tempor luctus.</p>
  </div>
</section>

<section class="testimonials">
  <div class="container">
    <h2>Testimonials</h2>
    <div class="testimonial-list">
      <article class="testimonial">
        <div class="testimonial-card">
          <svg class="quote-mark" viewBox="0 0 26 20" aria-hidden="true"><path d="M0 20V11C0 5 3 1 10 0v4c-3 1-5 3-5 6h5v10zM15 20V11c0-6 3-10 10-11v4c-3 1-5 3-5 6h5v10z" fill="#d6d6d6"/></svg>
          <p>Pellentesque laoreet nisi eu tellus eleifend aliquet. In a mi eget urna eleifend pulvinar id at quam. In vel diam vitae nunc lacinia commodo. Vestibulum non aliquet ex.</p>
        </div>
        <div class="testimonial-author"><strong>Mark Dale,</strong><span>Proin ac eros quis sem</span></div>
      </article>
      <article class="testimonial">
        <div class="testimonial-card">
          <svg class="quote-mark" viewBox="0 0 26 20" aria-hidden="true"><path d="M0 20V11C0 5 3 1 10 0v4c-3 1-5 3-5 6h5v10zM15 20V11c0-6 3-10 10-11v4c-3 1-5 3-5 6h5v10z" fill="#d6d6d6"/></svg>
          <p>Pellentesque laoreet nisi eu tellus eleifend aliquet. In a mi eget urna eleifend pulvinar id at quam. In vel diam vitae nunc lacinia commodo. Vestibulum non aliquet ex.</p>
        </div>
        <div class="testimonial-author"><strong>Mark Dale,</strong><span>Proin ac eros quis sem</span></div>
      </article>
      <article class="testimonial">
        <div class="testimonial-card">
          <svg class="quote-mark" viewBox="0 0 26 20" aria-hidden="true"><path d="M0 20V11C0 5 3 1 10 0v4c-3 1-5 3-5 6h5v10zM15 20V11c0-6 3-10 10-11v4c-3 1-5 3-5 6h5v10z" fill="#d6d6d6"/></svg>
          <p>Pellentesque laoreet nisi eu tellus eleifend aliquet. In a mi eget urna eleifend pulvinar id at quam. In vel diam vitae nunc lacinia commodo. Vestibulum non aliquet ex.</p>
        </div>
        <div class="testimonial-author"><strong>Mark Dale,</strong><span>Proin ac eros quis sem</span></div>
      </article>
    </div>
    <div class="testimonial-dots"><span class="active"></span><span></span><span></span><span></span></div>
  </div>
</section>

<section class="cta">
  <h2>Donec efficitur blandit neque</h2>
  <span class="button">Read more</span>
</section>

<footer class="site-footer">
  <div class="social"><span></span><span></span><span></span></div>
  <div class="footer-nav">Home<span>|</span>About us<span>|</span>Trainings<span>|</span>Classes<span>|</span>Testimonials<span>|</span>Contact us</div>
  <div class="copyright">Copyright © 2016, Vireo Fitness. All rights reserved.</div>
</footer>

</body>
</html>
```